Gobal construction supply company needs new business card design

I need a business card design for my global supply company using an existing logo. i will be looking to print these on rounded corner cards with the black background version of my logo on the back. on the front white background, my logo again and my simple details.

```html
<!DOCTYPE html>
<html lang="en">
<head>
<meta charset="utf-8">
<title>Northgate Supply Co. – Business Card</title>
<link rel="stylesheet" href="https://fonts.googleapis.com/css2?family=Montserrat:wght@600;700&family=Open+Sans:wght@400&display=swap">
<style>
  :root {
    --page-bg: #e9e7e4;
    --card-white: #f6f6f5;
    --card-dark: #1c1c1c;
    --accent-red: #e3111b;
    --text-light: #f2f2f2;
    --text-dark: #161616;
  }
  * { margin: 0; padding: 0; box-sizing: border-box; }
  html, body {
    width: 1200px;
    height: 900px;
    overflow: hidden;
    background: var(--page-bg);
  }
  .canvas {
    position: relative;
    width: 1200px;
    height: 900px;
  }
  .business-card {
    position: absolute;
    left: 180px;
    top: 210px;
    width: 840px;
    height: 480px;
    background: var(--card-white);
    border-radius: 4px;
    overflow: hidden;
    box-shadow: 0 10px 30px rgba(0,0,0,0.15);
  }
  .card-shapes {
    position: absolute;
    inset: 0;
  }
  .contact-block {
    position: absolute;
    left: 48px;
    top: 210px;
    color: var(--text-light);
    font-family: "Open Sans", sans-serif;
  }
  .person-name {
    font-family: "Montserrat", sans-serif;
    font-weight: 600;
    font-size: 25px;
    letter-spacing: 0.3px;
    color: var(--accent-red);
    line-height: 1.1;
    text-transform: uppercase;
  }
  .person-title {
    font-size: 21px;
    line-height: 1.3;
    margin-top: 2px;
  }
  .contact-list {
    list-style: none;
    margin-top: 42px;
  }
  .contact-item {
    display: flex;
    align-items: center;
    gap: 10px;
    font-size: 21px;
    line-height: 28px;
  }
  .contact-icon {
    width: 16px;
    height: 16px;
    flex: none;
    fill: var(--accent-red);
  }
  .brand-block {
    position: absolute;
    left: 420px;
    top: 178px;
    width: 400px;
    display: flex;
    justify-content: center;
    align-items: center;
    gap: 12px;
  }
  .brand-dot {
    width: 22px;
    height: 22px;
    border-radius: 50%;
    background: var(--accent-red);
  }
  .brand-name {
    font-family: "Montserrat", sans-serif;
    font-weight: 700;
    font-size: 25px;
    color: var(--text-dark);
    text-transform: uppercase;
    letter-spacing: 0.3px;
  }
</style>
</head>
<body>
<main class="canvas">
  <section class="business-card">
    <svg class="card-shapes" width="840" height="480" viewBox="0 0 840 480" aria-hidden="true">
      <polygon class="dark-panel" points="0,0 252,0 504,480 0,480" fill="var(--card-dark)"/>
      <polygon class="accent-stripe" points="252,0 258,0 510,480 504,480" fill="var(--accent-red)"/>
    </svg>

    <div class="contact-block">
      <h1 class="person-name">Daniel Hartley</h1>
      <p class="person-title">Managing Director</p>
      <ul class="contact-list">
        <li class="contact-item">
          <svg class="contact-icon" viewBox="0 0 16 16" aria-hidden="true"><path d="M1 6c0-2 3-4 7-4s7 2 7 4v1h-3V5.5H4V7H1z"/><path d="M3 8h10l1 6H2z"/></svg>
          044-987 654 321
        </li>
        <li class="contact-item">
          <svg class="contact-icon" viewBox="0 0 16 16" aria-hidden="true"><path d="M4 0h8a1 1 0 0 1 1 1v14a1 1 0 0 1-1 1H4a1 1 0 0 1-1-1V1a1 1 0 0 1 1-1zm1 2v10h6V2zm3 11a1 1 0 1 0 0 2 1 1 0 0 0 0-2z"/></svg>
          044-987 654 321
        </li>
        <li class="contact-item">
          <svg class="contact-icon" viewBox="0 0 16 16" aria-hidden="true"><path d="M1 3h14v1L8 9 1 4z"/><path d="M1 6l7 5 7-5v7H1z"/></svg>
          hello@northgatesupply.com
        </li>
        <li class="contact-item">
          <svg class="contact-icon" viewBox="0 0 16 16" aria-hidden="true"><circle cx="8" cy="8" r="7"/><path d="M1 8h14M8 1c-3 3-3 11 0 14M8 1c3 3 3 11 0 14" stroke="var(--card-dark)" stroke-width="1.2" fill="none"/></svg>
          www.northgatesupply.com
        </li>
      </ul>
    </div>

    <div class="brand-block">
      <span class="brand-dot"></span>
      <span class="brand-name">Northgate Supply Co.</span>
    </div>
  </section>
</main>
</body>
</html>
```